Mobile welding fabrication and repair, heavy equipment and semi repair

We need a business card design that will catch the eye but look prelesional at the same time. Were based out of Idaho and we do all welding fabrication jobs and repairs, we also build and install custom pipe fences for personal or larger scale fence jobs and can give free quotes. We can do semi truck and trailer repairs Mobily also.

Target Market(s)

Welding

Industry/Entity Type

welding and repair

Contact Information for Business Card

email (ravenforgeandmend@mailbay.net, phone number 208-417-3826, owner (Dalton Whitcomb), Pipe Fence, Semi Repair, Mobile welding and fabrication

Font styles to use
Sans Serif

Requirements
Must have
• My logo in black background on one side , and other side my logo in white back round with all the information listed on card details
Nice to have
• make it stand out from other business cards

```html
<!DOCTYPE html>
<html lang="en">
<head>
<meta charset="utf-8">
<title>Raven Forge and Mend — Business Card</title>
<link href="https://fonts.googleapis.com/css2?family=Lato:wght@400;700;900&display=swap" rel="stylesheet">
<style>
  :root {
    --backdrop: #2a2a2c;
    --card: #1b1c1e;
    --brand-blue: #1a86dc;
    --text-light: #ececec;
    --text-soft: #bfc1c4;
    --rule: #55575b;
  }
  * { margin: 0; padding: 0; box-sizing: border-box; }
  html, body { width: 1200px; height: 1108px; overflow: hidden; }
  body {
    background: var(--backdrop);
    font-family: "Lato", sans-serif;
    position: relative;
  }
  .card {
    position: absolute;
    top: 230px;
    width: 380px;
    height: 648px;
    background: var(--card);
    border-radius: 24px;
    box-shadow: 0 18px 40px rgba(0,0,0,.45);
    overflow: hidden;
  }
  .card--front { left: 180px; }
  .card--back { left: 640px; display: flex; align-items: center; justify-content: center; }

  .wordmark {
    position: absolute;
    top: 150px;
    left: 0; right: 0;
    text-align: center;
    color: var(--brand-blue);
    font-weight: 900;
    text-transform: uppercase;
    font-size: 36px;
    line-height: 1.1;
    letter-spacing: 1px;
  }
  .details {
    position: absolute;
    top: 372px;
    left: 0; right: 0;
    text-align: center;
  }
  .owner-name {
    color: var(--brand-blue);
    font-weight: 700;
    font-size: 25px;
    text-transform: uppercase;
    letter-spacing: .5px;
  }
  .owner-role {
    color: var(--text-light);
    font-size: 17px;
    text-transform: uppercase;
    margin-top: 4px;
  }
  .rule {
    width: 70px;
    height: 1px;
    background: var(--rule);
    margin: 16px auto;
  }
  .contact {
    color: var(--text-light);
    font-size: 16px;
    line-height: 1.5;
  }
  .services {
    color: var(--text-light);
    font-size: 14px;
    text-transform: uppercase;
    line-height: 1.8;
  }
  .services .dot {
    display: inline-block;
    width: 8px; height: 8px;
    border-radius: 50%;
    background: var(--brand-blue);
    margin: 0 6px;
    vertical-align: middle;
  }
  .back-name {
    color: var(--brand-blue);
    font-weight: 900;
    font-size: 30px;
    text-transform: uppercase;
    letter-spacing: 1px;
  }
</style>
</head>
<body>
  <section class="card card--front">
    <div class="wordmark">Raven<br>Forge and Mend</div>
    <div class="details">
      <div class="owner-name">Dalton Whitcomb</div>
      <div class="owner-role">Owner</div>
      <div class="rule"></div>
      <div class="contact">
        <div class="contact-phone">208-417-3826</div>
        <div class="contact-email">ravenforgeandmend@mailbay.net</div>
      </div>
      <div class="rule"></div>
      <div class="services">
        <div>Fabrication<span class="dot"></span>Mobile Welding</div>
        <div>Semi Repair<span class="dot"></span>Pipe Fence</div>
      </div>
    </div>
  </section>

  <section class="card card--back">
    <div class="back-name">Raven</div>
  </section>
</body>
</html>
```